Need Help having my business card stand out

I am the owner of Birchway Canine Training and would like for my business cards to stand out. I have been trying to keep designing them myself but I can't get what I have in my head on the card. I will try my best to post templates that I like for inspirations. I want something unique but elegant. I don't want in to look cartoony or cheesy. It needs to pop in a pet shop but also in a coffee shop or gym.

Target Market(s)

Dog owners, Married ,No young kids Jr High school kids and up (maybe kids on the way) Executives, Stay at home moms/wives, Small business owners

Industry/Entity Type

Dog Training

Contact Information for Business Card

Lowell Spratt, 281-904-3376, info@birchwaycanine.example, www.birchwaycanine.example

Colors

Designer to choose colors to be used in the design.

Requirements
Must have
• my logo
Should not have
• Cursive lettering

```html
<!DOCTYPE html>
<html lang="en">
<head>
<meta charset="utf-8">
<title>Birchway Canine Training – Business Card</title>
<link href="https://fonts.googleapis.com/css2?family=Open+Sans:wght@400;600;700&family=Josefin+Sans:wght@400;600&display=swap" rel="stylesheet">
<style>
  :root {
    --backdrop: #8a8a8a;
    --card: #323335;
    --card-edge: #2a2b2d;
    --rule: #6a6a6c;
    --band: #4b4747;
    --ink: #ffffff;
    --ink-soft: #e6e6e6;
    --mark-faint: #5c5c5e;
  }
  * { margin: 0; padding: 0; box-sizing: border-box; }
  html, body { width: 1200px; height: 900px; overflow: hidden; }
  body {
    background: var(--backdrop);
    font-family: "Open Sans", sans-serif;
    color: var(--ink);
    position: relative;
  }
  .card {
    position: absolute;
    left: 230px;
    width: 740px;
    height: 423px;
    background: var(--card);
    border: 1px solid var(--card-edge);
    overflow: hidden;
  }
  .card--front { top: 18px; }
  .card--back { top: 459px; }

  /* Front */
  .front-rule {
    position: absolute;
    top: 196px;
    height: 2px;
    background: var(--rule);
  }
  .front-rule--left { left: 0; width: 150px; }
  .front-rule--right { right: 0; width: 170px; top: 186px; }
  .brand {
    position: absolute;
    left: 0; right: 0;
    top: 140px;
    text-align: center;
  }
  .brand__tagline {
    font-family: "Josefin Sans", sans-serif;
    font-size: 13px;
    letter-spacing: 3px;
    text-transform: uppercase;
    color: var(--ink-soft);
    margin-bottom: 14px;
  }
  .brand__name {
    font-family: "Open Sans", sans-serif;
    font-weight: 700;
    font-size: 38px;
    line-height: 1.1;
    color: var(--ink);
  }

  /* Back */
  .back-divider {
    position: absolute;
    left: 340px;
    top: 0;
    width: 2px;
    height: 100%;
    background: var(--rule);
  }
  .back-mark {
    position: absolute;
    left: 30px;
    width: 290px;
    top: 170px;
    text-align: center;
    font-family: "Open Sans", sans-serif;
    font-weight: 700;
    font-size: 32px;
    line-height: 1.15;
    color: var(--mark-faint);
  }
  .name-band {
    position: absolute;
    left: 400px;
    right: 0;
    top: 40px;
    height: 88px;
    background: var(--band);
    text-align: right;
    padding: 14px 66px 0 0;
  }
  .name-band__name {
    font-size: 25px;
    font-weight: 400;
    color: var(--ink);
    line-height: 1.2;
  }
  .name-band__name b { font-weight: 700; }
  .name-band__role {
    font-family: "Josefin Sans", sans-serif;
    font-size: 17px;
    font-variant: small-caps;
    letter-spacing: 1px;
    color: var(--ink-soft);
  }
  .contacts {
    position: absolute;
    right: 84px;
    top: 148px;
    list-style: none;
    text-align: right;
  }
  .contacts li {
    font-size: 15px;
    color: var(--ink-soft);
    line-height: 28px;
    display: flex;
    justify-content: flex-end;
    align-items: center;
    gap: 12px;
  }
  .contacts li.gap { margin-top: 26px; }
  .contacts svg { width: 17px; height: 17px; fill: var(--ink-soft); flex: none; }
  .contacts .address { line-height: 30px; align-items: flex-start; }
  .contacts .address span { display: block; }
  .contacts .address svg { margin-top: 6px; }
</style>
</head>
<body>

<section class="card card--front" aria-label="Card front">
  <div class="front-rule front-rule--left"></div>
  <div class="front-rule front-rule--right"></div>
  <div class="brand">
    <p class="brand__tagline">Calm dogs, happy homes</p>
    <p class="brand__name">Birchway Canine<br>Training</p>
  </div>
</section>

<section class="card card--back" aria-label="Card back">
  <p class="back-mark">Birchway Canine<br>Training</p>
  <div class="back-divider"></div>

  <div class="name-band">
    <p class="name-band__name"><b>Lowell</b> Spratt</p>
    <p class="name-band__role">Designation</p>
  </div>

  <ul class="contacts">
    <li>281.904.3376
      <svg viewBox="0 0 24 24"><path d="M2 9c0-3 4-5 10-5s10 2 10 5v2h-5V9c0-1-2-1.5-5-1.5S7 8 7 9v2H2z M6 12h12l2 8H4z"/></svg>
    </li>
    <li>281.904.3377
      <svg viewBox="0 0 24 24"><path d="M7 3h10v5H7z M3 9h18v9h-3v3H6v-3H3z M8 15v4h8v-4z"/></svg>
    </li>
    <li class="gap">info@birchwaycanine.example
      <svg viewBox="0 0 24 24"><path d="M2 5h20v14H2z M3.5 6.5 12 13l8.5-6.5" fill="none" stroke="#e6e6e6" stroke-width="1.8"/><path d="M2 5h20l-10 8z"/></svg>
    </li>
    <li>www.birchwaycanine.example
      <svg viewBox="0 0 24 24"><circle cx="12" cy="12" r="9" fill="none" stroke="#e6e6e6" stroke-width="1.8"/><path d="M3 12h18M12 3c-4 4-4 14 0 18M12 3c4 4 4 14 0 18" fill="none" stroke="#e6e6e6" stroke-width="1.5"/></svg>
    </li>
    <li class="gap address">
      <span>000 Alder Row, Suite 120,<br>Fairbrook, US 0000</span>
      <svg viewBox="0 0 24 24"><path d="M12 2a7 7 0 0 0-7 7c0 5 7 13 7 13s7-8 7-13a7 7 0 0 0-7-7zm0 10a3 3 0 1 1 0-6 3 3 0 0 1 0 6z"/></svg>
    </li>
  </ul>
</section>

</body>
</html>
```